Logo and Flyer design Helix Summit Australia 2019

A logo and flyer design for a 3D Medical printing conference to be held in Melbourne Australia. The conference audience is aimed at people who have an interesting in 3D printing to benefit their work as well as printing for a hobby. Mostly professionals in the medical, bio-engineering, VET sciences fields who are 3D printing models for patients and simulation will attend this conference.

Target Market(s)

medical, bio-engineering, VET sciences fields who are 3D printing models for patients and simulation will attend this conference.

Industry/Entity Type

Medical And Science

Font styles to use
Sans Serif

Colors
3276b5
e34197
fbee3d
f68d4c
f04a50

Requirements
Must have
• Helix Summit logo
• Jaw
• Futuristic theme
• Helix Summit colours
Nice to have
• Unique design
Should not have
• Pictures from google images

```html
<!DOCTYPE html>
<html lang="en">
<head>
<meta charset="utf-8">
<title>Helix Summit Australia 2019 – Poster</title>
<link href="https://fonts.googleapis.com/css2?family=Audiowide&family=Oswald:wght@500;600&family=Open+Sans:wght@700&display=swap" rel="stylesheet">
<style>
  :root {
    --page-bg: #2a2a2c;
    --teal: #0f6f74;
    --teal-light: #2fa3a6;
    --navy: #15204f;
    --deep-purple: #2a1442;
    --crimson: #b0093b;
    --maroon: #5a0f35;
    --white: #ffffff;
    --strip: #e9e9ec;
    --brand-red: #9c0f3a;
    --brand-navy: #1a2350;
  }
  html, body {
    margin: 0;
    width: 1200px;
    height: 900px;
    overflow: hidden;
    background: var(--page-bg);
  }
  .poster {
    position: absolute;
    left: 300px;
    top: 30px;
    width: 600px;
    height: 840px;
    box-shadow: 0 20px 50px rgba(0,0,0,.5);
  }
  .poster svg { display: block; }
  .eyebrow { font-family: "Oswald", sans-serif; font-weight: 500; }
  .title { font-family: "Audiowide", sans-serif; }
  .band-text { font-family: "Oswald", sans-serif; font-weight: 600; }
  .brand-name { font-family: "Open Sans", sans-serif; font-weight: 700; }
</style>
</head>
<body>
<main class="poster">
  <svg width="600" height="840" viewBox="0 0 600 840" xmlns="http://www.w3.org/2000/svg">
    <defs>
      <linearGradient id="poster-bg" x1="0" y1="0" x2="1" y2="0.6">
        <stop offset="0" stop-color="var(--teal-light)"/>
        <stop offset="0.45" stop-color="var(--teal)"/>
        <stop offset="1" stop-color="var(--navy)"/>
      </linearGradient>
      <linearGradient id="band-fade" x1="0" y1="0" x2="1" y2="0">
        <stop offset="0" stop-color="var(--deep-purple)"/>
        <stop offset="0.35" stop-color="var(--maroon)"/>
        <stop offset="0.7" stop-color="var(--crimson)"/>
        <stop offset="1" stop-color="var(--crimson)"/>
      </linearGradient>
      <linearGradient id="band-fade-low" x1="0" y1="0" x2="1" y2="0">
        <stop offset="0" stop-color="var(--crimson)"/>
        <stop offset="0.55" stop-color="var(--crimson)"/>
        <stop offset="1" stop-color="var(--deep-purple)"/>
      </linearGradient>
      <radialGradient id="jaw-area" cx="0.5" cy="0.45" r="0.6">
        <stop offset="0" stop-color="#f4f2ec"/>
        <stop offset="0.6" stop-color="#e8e4d6"/>
        <stop offset="1" stop-color="#d9c9a0"/>
      </radialGradient>
    </defs>

    <rect class="poster-bg" width="600" height="770" fill="url(#poster-bg)"/>
    <polygon class="shade-band" points="0,560 600,300 600,430 0,690" fill="var(--navy)" opacity="0.35"/>

    <polygon class="date-band" points="0,460 600,200 600,268 0,528" fill="url(#band-fade)"/>
    <polygon class="lower-band" points="0,690 600,430 600,498 0,758" fill="url(#band-fade-low)"/>

    <g class="headline" transform="rotate(-14 300 160)">
      <text class="eyebrow" x="300" y="108" text-anchor="middle" font-size="15" fill="var(--white)" letter-spacing="0.5">5TH ANNUAL CONFERANCE</text>
      <text class="title" x="300" y="170" text-anchor="middle" font-size="58" fill="var(--white)" letter-spacing="1">HELIX SUMMIT</text>
      <text class="title" x="300" y="228" text-anchor="middle" font-size="44" fill="var(--white)" letter-spacing="2">AUSTRALIA 2019</text>
    </g>

    <text class="band-text" transform="translate(300 372) rotate(-23.4)" text-anchor="middle" font-size="32" fill="var(--white)" dominant-baseline="middle">14-16 NOVEMBER 2019 , MELBOURNE</text>

    <circle class="jaw-ring" cx="285" cy="590" r="104" fill="var(--maroon)"/>
    <g class="jaw-model" role="img" aria-label="Photo of a 3D-printed amber resin jaw model on a white surface">
      <circle cx="285" cy="590" r="94" fill="url(#jaw-area)"/>
    </g>

    <rect class="brand-strip" y="770" width="600" height="70" fill="var(--strip)"/>
    <g class="brand">
      <circle cx="237" cy="805" r="17" fill="none" stroke="var(--brand-navy)" stroke-width="4"/>
      <text class="brand-name" x="262" y="814" font-size="25" fill="var(--brand-red)">Strata Lab</text>
    </g>
  </svg>
</main>
</body>
</html>
```